Letterhead, stationery and email signature for construction business

I need the letterhead, stationery and email signature designs for a construction business. I want them to have a corporate feel to them.

I've attached the logo for reference.

```html
<!DOCTYPE html>
<html lang="en">
<head>
<meta charset="utf-8">
<title>HTML Email Signature – Brackwell Projects</title>
<link rel="stylesheet" href="https://fonts.googleapis.com/css2?family=Marcellus&family=Montserrat:wght@400;600&family=Raleway:wght@700&family=Roboto:wght@400&display=swap">
<style>
  :root {
    --bg: #ffffff;
    --title: #3a3a3c;
    --brand-blue: #2c56a3;
    --text-grey: #6b6b6f;
    --role-grey: #4a4a4d;
    --divider: #4a4a4d;
  }
  * { margin: 0; padding: 0; box-sizing: border-box; }
  html, body { width: 1200px; height: 1200px; overflow: hidden; background: var(--bg); }
  .canvas { position: relative; width: 1200px; height: 1200px; }

  .sheet-title {
    position: absolute; top: 183px; left: 0; width: 1200px;
    text-align: center;
    font-family: "Marcellus", serif;
    font-weight: 400; font-size: 55px; letter-spacing: 1px;
    color: var(--title);
    -webkit-text-stroke: 1.2px var(--title);
  }

  .brand {
    position: absolute; left: 186px; top: 580px;
    display: flex; align-items: center; gap: 14px;
  }
  .brand-mark { width: 36px; height: 36px; border-radius: 50%; background: var(--brand-blue); flex: none; }
  .brand-name {
    font-family: "Montserrat", sans-serif; font-weight: 600;
    font-size: 30px; line-height: 40px;
    color: var(--brand-blue); white-space: nowrap;
  }

  .social-row {
    position: absolute; left: 309px; top: 673px;
    display: flex; gap: 7px;
  }
  .social-dot { width: 31px; height: 31px; border-radius: 50%; background: var(--brand-blue); }

  .divider {
    position: absolute; left: 611px; top: 438px;
    width: 2px; height: 324px; background: var(--divider);
  }

  .details { position: absolute; left: 647px; top: 438px; }
  .person-name {
    font-family: "Raleway", sans-serif; font-weight: 700;
    font-size: 34px; color: var(--brand-blue); line-height: 38px;
  }
  .person-role {
    font-family: "Roboto", sans-serif; font-size: 27px;
    color: var(--role-grey); line-height: 34px;
  }
  .company-address {
    margin-top: 22px;
    font-family: "Montserrat", sans-serif; font-size: 26px;
    color: var(--text-grey); line-height: 34px;
  }
  .contact-list { list-style: none; margin-top: 14px; }
  .contact-item {
    display: flex; align-items: center; gap: 7px;
    font-family: "Montserrat", sans-serif; font-size: 26px;
    color: var(--text-grey); line-height: 37.5px;
  }
  .contact-icon { width: 26px; height: 26px; flex: none; }
</style>
</head>
<body>
<div class="canvas">
  <h1 class="sheet-title">HTML EMAIL SIGNATURE</h1>

  <div class="brand">
    <span class="brand-mark"></span>
    <span class="brand-name">Brackwell Projects</span>
  </div>

  <div class="social-row" role="img" aria-label="Social network links">
    <span class="social-dot"></span>
    <span class="social-dot"></span>
    <span class="social-dot"></span>
    <span class="social-dot"></span>
  </div>

  <div class="divider"></div>

  <div class="details">
    <p class="person-name">DANIEL HARCOURT</p>
    <p class="person-role">Owner</p>
    <p class="company-address">Brackwell Project, Ltd.<br>Marlow House, 42 Kestrel<br>Ave, London SE14 7QT</p>
    <ul class="contact-list">
      <li class="contact-item">
        <svg class="contact-icon" viewBox="0 0 24 24" aria-hidden="true"><path fill="#2c56a3" d="M6.6 10.8a15.1 15.1 0 0 0 6.6 6.6l2.2-2.2a1 1 0 0 1 1-.25 11.4 11.4 0 0 0 3.6.57 1 1 0 0 1 1 1V20a1 1 0 0 1-1 1A17 17 0 0 1 3 4a1 1 0 0 1 1-1h3.5a1 1 0 0 1 1 1c0 1.25.2 2.45.57 3.57a1 1 0 0 1-.25 1z"/></svg>
        (555) 318-4062
      </li>
      <li class="contact-item">
        <svg class="contact-icon" viewBox="0 0 24 24" aria-hidden="true"><rect x="2.5" y="5.5" width="19" height="13" fill="none" stroke="#2c56a3" stroke-width="2"/><path d="M2.5 5.5l9.5 8 9.5-8M2.5 18.5l7-6.5M21.5 18.5l-7-6.5" fill="none" stroke="#2c56a3" stroke-width="1.6"/></svg>
        info@brackwell.com
      </li>
      <li class="contact-item">
        <svg class="contact-icon" viewBox="0 0 24 24" aria-hidden="true"><g fill="none" stroke="#2c56a3" stroke-width="1.6"><circle cx="12" cy="12" r="9.5"/><ellipse cx="12" cy="12" rx="4.2" ry="9.5"/><path d="M2.5 12h19M4 7h16M4 17h16"/></g></svg>
        www.brackwell.com
      </li>
    </ul>
  </div>
</div>
</body>
</html>
```